Coastline Premier Retreats Business Card Design

Design a business card for Coastline Premier Retreats. Look at the website for colors and reference. Card should have logo, name, title, office number, mobile number, email, URL and a tagline like, "Luxury Hotel & Resort Email Marketing" (This might change).

https://www.coastlinepremierretreats.example

The rest I will leave up to your imagination.

Contact Information for Business Card

Logo, name, title, office number, mobile number, email, URL and a tagline like, "Luxury Hotel & Resort Email Marketing" (This might change).

```html
<!DOCTYPE html>
<html lang="en">
<head>
<meta charset="utf-8">
<title>Coastline Premier Retreats – Business Card</title>
<link href="https://fonts.googleapis.com/css2?family=Arimo:wght@400;700&family=Montserrat:wght@400&display=swap" rel="stylesheet">
<style>
  :root {
    --backdrop: #262626;
    --card: #1b1b1b;
    --orange: #e8711a;
    --white: #f2f2f2;
  }
  * { margin: 0; padding: 0; box-sizing: border-box; }
  html, body { width: 1200px; height: 1059px; overflow: hidden; }
  body {
    background: var(--backdrop);
    position: relative;
    font-family: "Arimo", Arial, sans-serif;
    color: var(--white);
  }
  .card {
    position: absolute;
    background: var(--card);
    box-shadow: 0 10px 24px rgba(0,0,0,.6);
  }
  .card--front { left: 257px; top: 89px; width: 687px; height: 390px; }
  .card--back  { left: 253px; top: 546px; width: 694px; height: 395px; }

  .frame { position: absolute; left: 21px; top: 21px; width: 643px; height: 337px; }

  .brand-name {
    font-family: "Arimo", Arial, sans-serif;
    font-weight: 700;
    color: var(--white);
    text-transform: uppercase;
  }
  .card--front .brand-name {
    position: absolute; right: 53px; top: 60px;
    text-align: right; font-size: 18px; line-height: 22px; letter-spacing: 1.5px;
  }
  .card--back .brand-name {
    position: absolute; left: 0; right: 0; top: 150px;
    text-align: center; font-size: 38px; line-height: 46px; letter-spacing: 3px;
  }

  .person { position: absolute; left: 53px; top: 140px; }
  .person__name {
    font-weight: 700; font-size: 30px; line-height: 34px;
    color: var(--orange); letter-spacing: .3px;
  }
  .person__title {
    font-family: "Montserrat", Arial, sans-serif;
    font-size: 16px; line-height: 20px; margin-top: -1px; letter-spacing: .3px;
  }
  .divider {
    position: absolute; left: 53px; top: 211px; width: 581px; height: 1px;
    background: var(--orange);
  }
  .contacts { position: absolute; left: 53px; top: 228px; list-style: none; }
  .contacts li {
    display: flex; align-items: center; height: 25.3px;
    font-size: 16.5px;
  }
  .contacts svg { width: 11px; height: 12px; margin-right: 7px; fill: var(--orange); }
  .address {
    position: absolute; right: 53px; top: 256px; text-align: right;
    font-size: 16.5px; line-height: 21px; font-style: normal;
  }
  .tagline {
    position: absolute; left: 178px; width: 332px; top: 348px;
    text-align: center; font-size: 17px; line-height: 20px;
    color: var(--orange); background: var(--card);
  }
</style>
</head>
<body>
  <section class="card card--front">
    <svg class="frame" viewBox="0 0 643 337" aria-hidden="true">
      <polyline points="157,336 1,336 1,1 642,1 642,336 489,336" fill="none" stroke="#e8711a" stroke-width="2"/>
    </svg>
    <div class="brand-name">Coastline<br>Premier Retreats</div>

    <div class="person">
      <h1 class="person__name">MARCUS HALE</h1>
      <p class="person__title">CEO/Founder</p>
    </div>
    <div class="divider"></div>

    <ul class="contacts">
      <li><svg viewBox="0 0 11 12"><path d="M2.5 0h6a1 1 0 0 1 1 1v10a1 1 0 0 1-1 1h-6a1 1 0 0 1-1-1V1a1 1 0 0 1 1-1zm.5 1.5v8h5v-8zM5.5 10.2a.6.6 0 1 0 0 1.2.6.6 0 0 0 0-1.2z"/></svg>555.014.2200</li>
      <li><svg viewBox="0 0 11 12"><path d="M0 4.5C0 2.5 2.5 2 5.5 2S11 2.5 11 4.5H8.5V3.6h-6v.9zM2 5.5h7l1 5.5H1zm2 1.5v1h1V7zm2 0v1h1V7zM4 9v1h1V9zm2 0v1h1V9z"/></svg>+34 600 000 417</li>
      <li><svg viewBox="0 0 11 12"><path d="M5.5 1 11 5v6H0V5zM1.5 5.6l4 3 4-3-4-3z"/></svg>info@coastlinepremierretreats.example</li>
      <li><svg viewBox="0 0 11 12"><circle cx="5.5" cy="6" r="5.3"/></svg>www.coastlinepremierretreats.example</li>
    </ul>

    <address class="address">Po Box, 210 Shore Rd<br>North America, ZZ 10001</address>

    <p class="tagline">Luxury Hotel &amp; Resort Email Marketing</p>
  </section>

  <section class="card card--back">
    <div class="brand-name">Coastline<br>Premier Retreats</div>
  </section>
</body>
</html>
```